Brookmere Osteopathy flyer

I want a clean clear DL flyer (but also want an A4 poster) promoting a new Osteopathic business in a semi rural area in Tasmania (Australia).
It can have pictures like the examples attached to show people what Osteopathy is (its like Chiropractic and physiotherapy).
I am the sole practioner and am male, so any pictures would be best to be a white male if possible.
I've attached some wording, you can use all, or none of it
I don't have a phone number for the business yet
info@brookmereosteopathy.example
www.brookmereosteopathy.example
Target Market(s)
Australians, from tradies, professionals, babies to retired people
Industry/Entity Type
Health
Look and feel

```html
<!DOCTYPE html>
<html lang="en">
<head>
<meta charset="utf-8">
<title>Brookmere Osteopathy – DL Flyer</title>
<link href="https://fonts.googleapis.com/css2?family=Poppins:wght@400;500;600;700;800&display=swap" rel="stylesheet">
<style>
  :root {
    --orange: #f39237;
    --blue: #1395d2;
    --ink: #1f1f1f;
    --white: #ffffff;
    --backdrop: #6f6e70;
    --photo-light: #d9d4cf;
    --photo-dark: #9aa7b3;
  }
  * { margin: 0; padding: 0; box-sizing: border-box; }
  html, body { width: 1190px; height: 1200px; overflow: hidden; }
  body {
    background: var(--backdrop);
    font-family: "Poppins", sans-serif;
    color: var(--ink);
    position: relative;
  }
  .flyer {
    position: absolute;
    top: 141px;
    width: 432px;
    height: 917px;
    background: var(--white);
    overflow: hidden;
  }
  .flyer--front { left: 131px; }
  .flyer--back { left: 627px; }
  .flyer-art { position: absolute; inset: 0; width: 432px; height: 917px; }

  /* Front */
  .brand-mark {
    position: absolute;
    left: 141px; top: 57px;
    width: 150px; height: 150px;
    border: 2px solid var(--blue);
    border-radius: 50%;
    display: flex; align-items: center; justify-content: center;
    text-align: center;
  }
  .brand-name {
    font-weight: 600;
    font-size: 17px;
    line-height: 1.2;
    color: var(--blue);
  }
  .headline {
    position: absolute;
    left: 0; right: 0; top: 588px;
    text-align: center;
    font-weight: 700;
    line-height: 44px;
    letter-spacing: 0.5px;
  }
  .headline .line-1 { display: block; font-size: 49px; color: var(--orange); }
  .headline .line-2 { display: block; font-size: 53px; color: var(--blue); }
  .intro {
    position: absolute;
    left: 0; right: 0; top: 700px;
    text-align: center;
    font-size: 14.5px;
    line-height: 18px;
  }
  .phone-pill--front {
    position: absolute;
    left: 79px; top: 754px;
    width: 274px; height: 54px;
    background: var(--orange);
    border: 2px solid var(--white);
    border-radius: 12px;
    color: var(--white);
    font-size: 45px; font-weight: 500;
    line-height: 50px;
    text-align: center;
    letter-spacing: -1px;
  }
  .web-front {
    position: absolute;
    left: 0; right: 0; top: 828px;
    text-align: center;
    color: var(--white);
    font-weight: 700;
    font-size: 17px;
  }

  /* Back */
  .reasons-title {
    position: absolute;
    left: 56px; top: 222px;
    font-weight: 800;
    font-size: 24px;
    line-height: 26px;
    text-transform: uppercase;
  }
  .reasons-title .line-1 { display: block; color: var(--orange); }
  .reasons-title .line-2 { display: block; color: var(--blue); }
  .reason {
    position: absolute;
    display: flex; align-items: center;
    font-size: 14px;
    line-height: 17px;
    font-weight: 500;
  }
  .reason-icon {
    flex: none;
    width: 48px; height: 48px;
    border: 1.5px solid var(--blue);
    border-radius: 50%;
    margin-right: 12px;
  }
  .note-band {
    position: absolute;
    left: 0; right: 0; top: 640px; height: 67px;
    background: var(--orange);
    padding: 7px 56px 0 56px;
    font-size: 11px;
    line-height: 13.4px;
    font-weight: 500;
  }
  .contact-band {
    position: absolute;
    left: 0; right: 0; top: 707px; height: 123px;
    background: var(--blue);
  }
  .phone-pill--back {
    position: absolute;
    left: 78px; top: 0;
    width: 276px; height: 54px;
    background: var(--white);
    border-radius: 0 0 12px 12px;
    color: var(--blue);
    font-size: 45px; font-weight: 500;
    line-height: 56px;
    text-align: center;
    letter-spacing: -1px;
  }
  .contact-line {
    position: absolute;
    left: 56px;
    display: flex; align-items: center;
    color: var(--white);
    font-size: 17px;
  }
  .contact-line svg { margin-right: 9px; flex: none; }
  .contact-line--address { top: 64px; }
  .contact-line--email { top: 88px; }
  .web-back {
    position: absolute;
    left: 0; right: 0; top: 830px; height: 87px;
    background: var(--orange);
    color: var(--white);
    text-align: center;
    padding-top: 10px;
    font-size: 19px;
  }
  .web-back strong { font-weight: 700; }
</style>
</head>
<body>

<section class="flyer flyer--front">
  <svg class="flyer-art" viewBox="0 0 432 917" aria-hidden="false">
    <defs>
      <linearGradient id="frontPhoto" x1="0" y1="0" x2="1" y2="1">
        <stop offset="0" stop-color="#cfc8c1"/>
        <stop offset="0.5" stop-color="#b9c4cf"/>
        <stop offset="1" stop-color="#d8cfc6"/>
      </linearGradient>
      <linearGradient id="thumbPhoto" x1="0" y1="0" x2="1" y2="1">
        <stop offset="0" stop-color="#c9c2bb"/>
        <stop offset="1" stop-color="#9fb1c2"/>
      </linearGradient>
    </defs>
    <rect x="0" y="160" width="432" height="420" fill="url(#frontPhoto)" role="img" aria-label="Photo: osteopath treating a patient's lower back on a treatment table"/>
    <path d="M0 0 H432 V165 Q260 255 0 180 Z" fill="#ffffff"/>
    <path d="M0 180 Q260 255 432 165" fill="none" stroke="var(--orange)" stroke-width="8"/>
    <path d="M0 560 Q216 470 432 588 V917 H0 Z" fill="#ffffff"/>
    <path d="M0 560 Q216 470 432 588" fill="none" stroke="var(--blue)" stroke-width="10"/>
    <rect x="0" y="787" width="432" height="130" fill="var(--blue)"/>
    <g stroke="#ffffff" stroke-width="4">
      <circle cx="99" cy="529" r="47" fill="url(#thumbPhoto)" role="img" aria-label="Photo: shoulder assessment"/>
      <circle cx="212" cy="529" r="54" fill="url(#thumbPhoto)" role="img" aria-label="Photo: neck and shoulder treatment"/>
      <circle cx="325" cy="529" r="47" fill="url(#thumbPhoto)" role="img" aria-label="Photo: leg stretch with practitioner"/>
    </g>
  </svg>
  <div class="brand-mark"><span class="brand-name">Brookmere<br>Osteopathy</span></div>
  <h1 class="headline"><span class="line-1">Feel Better</span><span class="line-2">Move Freely</span></h1>
  <p class="intro">Discover how osteopathy can help relieve<br>your pain and restore your movement.</p>
  <div class="phone-pill--front">1234567890</div>
  <div class="web-front">www.brookmereosteopathy.example</div>
</section>

<section class="flyer flyer--back">
  <svg class="flyer-art" viewBox="0 0 432 917">
    <defs>
      <linearGradient id="backPhoto" x1="0" y1="0" x2="1" y2="0">
        <stop offset="0" stop-color="#a9c3d8"/>
        <stop offset="0.5" stop-color="#cdd3d6"/>
        <stop offset="1" stop-color="#b7c9d4"/>
      </linearGradient>
    </defs>
    <rect x="0" y="0" width="432" height="220" fill="url(#backPhoto)" role="img" aria-label="Photo: osteopath assessing a standing patient's back"/>
    <path d="M0 110 Q150 240 432 135 V917 H0 Z" fill="#ffffff"/>
    <path d="M0 110 Q150 240 432 135" fill="none" stroke="var(--orange)" stroke-width="10"/>
    <path d="M0 128 Q170 265 432 150" fill="none" stroke="var(--blue)" stroke-width="14"/>
  </svg>

  <h2 class="reasons-title"><span class="line-1">Common reasons people</span><span class="line-2">visit an osteopath:</span></h2>

  <div class="reason" style="left:54px; top:292px;"><span class="reason-icon"></span>Back or<br>neck pain</div>
  <div class="reason" style="left:238px; top:292px;"><span class="reason-icon"></span>Sciatica</div>
  <div class="reason" style="left:54px; top:361px;"><span class="reason-icon"></span>Headaches<br>or migraines</div>
  <div class="reason" style="left:238px; top:361px;"><span class="reason-icon"></span>Plantar<br>fasciitis</div>
  <div class="reason" style="left:54px; top:430px;"><span class="reason-icon"></span>Joint &amp;<br>muscle pain</div>
  <div class="reason" style="left:238px; top:430px;"><span class="reason-icon"></span>Tendonitis<br>or Bursitis</div>
  <div class="reason" style="left:54px; top:498px;"><span class="reason-icon"></span>Pregnancy<br>related<br>discomfort</div>
  <div class="reason" style="left:238px; top:498px;"><span class="reason-icon"></span>Adhesive<br>capsulitis</div>
  <div class="reason" style="left:54px; top:566px;"><span class="reason-icon"></span>Disc related<br>issues</div>
  <div class="reason" style="left:238px; top:566px;"><span class="reason-icon"></span>Tennis or<br>Golfers<br>elbow</div>

  <p class="note-band">Osteopaths use a combination of joint manipulation, targeted deep tissue massage and stretching to improve function, relieve pain and support the body's ability to heal itself.</p>

  <div class="contact-band">
    <div class="phone-pill--back">1234567890</div>
    <div class="contact-line contact-line--address">
      <svg width="12" height="14" viewBox="0 0 12 14"><path d="M6 0a5.5 5.5 0 0 0-5.5 5.5C.5 9.5 6 14 6 14s5.5-4.5 5.5-8.5A5.5 5.5 0 0 0 6 0Z" fill="#fff"/><circle cx="6" cy="5.5" r="2" fill="var(--blue)"/></svg>
      24 Willow Creek road, Brookmere
    </div>
    <div class="contact-line contact-line--email">
      <svg width="13" height="13" viewBox="0 0 13 13"><circle cx="6.5" cy="6.5" r="6.5" fill="#fff"/><rect x="3" y="4.2" width="7" height="4.6" fill="none" stroke="var(--blue)" stroke-width="1"/><path d="M3 4.2l3.5 2.6L10 4.2" fill="none" stroke="var(--blue)" stroke-width="1"/></svg>
      info@brookmereosteopathy.example
    </div>
  </div>

  <div class="web-back">www.<strong>brookmereosteopathy</strong>.example</div>
</section>

</body>
</html>
```